Flyer for the Lumen 2025 Conference

I am looking to produce a flyer for our upcoming conference, Lumen 2025. This is an annual conference that we plan to publicize on social media. The ideal designer will create a flyer that is eye-catching and effectively communicates the key information. Please see attached our logo, speaker photo, and flyer content.

Target Market(s)

All demographics

Industry/Entity Type

Christian

Font styles to use
Sans Serif

Requirements
Should not have
• Cross, church

```html
<!DOCTYPE html>
<html lang="en">
<head>
<meta charset="utf-8">
<title>Lumen 2025 Conference</title>
<link href="https://fonts.googleapis.com/css2?family=Montserrat:wght@400;500;600;700;800&display=swap" rel="stylesheet">
<style>
  :root {
    --night: #0b0c1e;
    --navy: #1a1c3e;
    --ember: #7a3424;
    --gold: #e8c24a;
    --gold-deep: #a9801f;
    --gold-light: #fbe7a0;
    --date-yellow: #f3cf4a;
    --white: #ffffff;
    --speaker-gold: #c9a23a;
    --speaker-blue: #1f4fb0;
  }
  * { margin: 0; padding: 0; box-sizing: border-box; }
  html, body { width: 876px; height: 1200px; overflow: hidden; background: var(--night); }
  body { font-family: "Montserrat", sans-serif; color: var(--white); }
  .flyer {
    position: relative; width: 876px; height: 1200px; overflow: hidden;
    background: linear-gradient(180deg, var(--navy) 0%, #2a2040 30%, #3a2436 52%, var(--ember) 68%, #1a0e10 82%, #050506 100%);
  }
  .venue-scene {
    position: absolute; inset: 0 0 420px 0;
    background: radial-gradient(ellipse at 45% 30%, rgba(140,100,80,.45), transparent 60%),
                radial-gradient(ellipse at 50% 85%, rgba(240,120,50,.35), transparent 55%);
  }
  .brand-name {
    position: absolute; left: 100px; top: 152px;
    font-weight: 600; font-size: 66px; letter-spacing: 1px; color: var(--white); line-height: 1;
  }
  .speaker {
    position: absolute; left: 540px; top: 68px; width: 262px; height: 262px; border-radius: 50%;
    border: 6px solid var(--gold);
    background: radial-gradient(circle at 40% 35%, #d8b34a 0%, var(--speaker-gold) 50%, var(--speaker-blue) 100%);
  }
  .title-word {
    position: absolute; left: 92px; top: 318px; font-weight: 800; font-size: 168px; letter-spacing: 2px; line-height: 1;
    color: var(--gold);
    background: linear-gradient(180deg, var(--gold-light) 0%, var(--gold) 45%, var(--gold-deep) 100%);
    -webkit-background-clip: text; background-clip: text; -webkit-text-fill-color: transparent;
  }
  .title-year {
    position: absolute; left: 160px; top: 478px; font-weight: 800; font-size: 124px; line-height: 1;
    background: linear-gradient(180deg, var(--gold-light) 0%, var(--gold) 45%, var(--gold-deep) 100%);
    -webkit-background-clip: text; background-clip: text; -webkit-text-fill-color: transparent;
  }
  .title-label { position: absolute; left: 505px; top: 492px; font-weight: 500; font-size: 26px; letter-spacing: 1.5px; }
  .theme { position: absolute; left: 178px; top: 600px; font-weight: 500; font-size: 26px; letter-spacing: 2px; }
  .divider { position: absolute; left: 60px; top: 605px; width: 750px; height: 60px; }
  .schedule { position: absolute; left: 98px; top: 715px; list-style: none; }
  .session { display: flex; align-items: center; gap: 22px; height: 88px; }
  .session-icon { width: 66px; height: 58px; flex: none; }
  .session-day { color: var(--date-yellow); font-size: 21px; font-weight: 500; }
  .session-time { font-size: 21px; font-weight: 500; }
  .location { position: absolute; left: 482px; top: 978px; display: flex; gap: 24px; }
  .location-pin { width: 52px; height: 80px; flex: none; }
  .location-text { font-size: 17px; line-height: 1.3; font-style: normal; }
  .download {
    position: absolute; left: 20px; top: 1055px; width: 450px; height: 48px;
    background: linear-gradient(90deg, var(--gold-deep), var(--gold-light) 40%, var(--gold) 75%, transparent);
    clip-path: polygon(4% 0, 100% 0, 96% 100%, 0 100%);
    display: flex; align-items: center; padding-left: 34px;
    color: #2a2010; font-weight: 800; font-size: 22px; letter-spacing: 1px;
  }
  .footer { position: absolute; left: 0; right: 0; top: 1118px; text-align: center; font-size: 17px; font-weight: 600; }
  .footer span { margin: 0 12px; }
</style>
</head>
<body>
<main class="flyer">
  <div class="venue-scene" role="img" aria-label="Night view of a lit performing arts venue with stage lighting"></div>

  <div class="brand-name">VESTRA</div>

  <div class="speaker" role="img" aria-label="Portrait photo of the conference speaker in a blue suit"></div>

  <h1>
    <span class="title-word">LUMEN</span>
    <span class="title-year">2025</span>
    <span class="title-label">CONFERENCE</span>
  </h1>
  <p class="theme">THE VOICE OF THE LORD</p>

  <svg class="divider" viewBox="0 0 750 60" aria-hidden="true">
    <line x1="20" y1="42" x2="730" y2="42" stroke="#d8b04a" stroke-width="3"/>
    <circle cx="20" cy="42" r="5" fill="#d8b04a"/>
    <circle cx="730" cy="42" r="5" fill="#d8b04a"/>
  </svg>

  <ul class="schedule">
    <li class="session">
      <svg class="session-icon" viewBox="0 0 66 58" aria-hidden="true"><rect x="2" y="8" width="50" height="44" rx="4" fill="none" stroke="#e8c24a" stroke-width="4"/><rect x="2" y="8" width="50" height="10" fill="#e8c24a"/><line x1="14" y1="2" x2="14" y2="12" stroke="#e8c24a" stroke-width="4"/><line x1="40" y1="2" x2="40" y2="12" stroke="#e8c24a" stroke-width="4"/><circle cx="50" cy="44" r="12" fill="#0b0c1e" stroke="#e8c24a" stroke-width="3"/><path d="M50 37v7h6" stroke="#e8c24a" stroke-width="3" fill="none"/></svg>
      <div><div class="session-day">FRIDAY, DECEMBER 26TH,</div><div class="session-time">6:30PM - 9:00PM</div></div>
    </li>
    <li class="session">
      <svg class="session-icon" viewBox="0 0 66 58" aria-hidden="true"><rect x="2" y="8" width="50" height="44" rx="4" fill="none" stroke="#e8c24a" stroke-width="4"/><rect x="2" y="8" width="50" height="10" fill="#e8c24a"/><line x1="14" y1="2" x2="14" y2="12" stroke="#e8c24a" stroke-width="4"/><line x1="40" y1="2" x2="40" y2="12" stroke="#e8c24a" stroke-width="4"/><circle cx="50" cy="44" r="12" fill="#0b0c1e" stroke="#e8c24a" stroke-width="3"/><path d="M50 37v7h6" stroke="#e8c24a" stroke-width="3" fill="none"/></svg>
      <div><div class="session-day">SATURDAY, DECEMBER 27TH,</div><div class="session-time">5:30PM - 8:00PM</div></div>
    </li>
    <li class="session">
      <svg class="session-icon" viewBox="0 0 66 58" aria-hidden="true"><rect x="2" y="8" width="50" height="44" rx="4" fill="none" stroke="#e8c24a" stroke-width="4"/><rect x="2" y="8" width="50" height="10" fill="#e8c24a"/><line x1="14" y1="2" x2="14" y2="12" stroke="#e8c24a" stroke-width="4"/><line x1="40" y1="2" x2="40" y2="12" stroke="#e8c24a" stroke-width="4"/><circle cx="50" cy="44" r="12" fill="#0b0c1e" stroke="#e8c24a" stroke-width="3"/><path d="M50 37v7h6" stroke="#e8c24a" stroke-width="3" fill="none"/></svg>
      <div><div class="session-day">SUNDAY, DECEMBER 29TH,</div><div class="session-time">4:30PM - 7:00PM</div></div>
    </li>
  </ul>

  <div class="location">
    <svg class="location-pin" viewBox="0 0 52 80" aria-hidden="true"><path d="M26 2C12 2 2 12 2 26c0 18 24 50 24 50s24-32 24-50C50 12 40 2 26 2z" fill="#e8c24a"/><circle cx="26" cy="25" r="9" fill="#0b0c1e"/></svg>
    <address class="location-text">The Harborview Performing<br>&nbsp;Arts Center<br>218 Linden Mill Road<br>Harborview, Maine 04099</address>
  </div>

  <div class="download">DOWNLOAD | VESTRA</div>

  <p class="footer"><span>Tel 5550-0142</span>|<span>contact vestra app and letter</span>|<span>www.vestra.org</span></p>
</main>
</body>
</html>
```